FunBrixo Business Card

We need a business card design for our company. We sell construction-themed amusement rides for kids.

Contact Information for Business Card

Contact info on business card should include:
Carl Dunning
Co-Founder & COO
(833) 571-FUNBRIX
Carl@funbrixo-demo.com
www.funbrixo-demo.com

```html
<!DOCTYPE html>
<html lang="en">
<head>
<meta charset="utf-8">
<title>FunBrixo Business Card</title>
<link rel="stylesheet" href="https://fonts.googleapis.com/css2?family=Arimo:wght@400;700&display=swap">
<style>
  :root {
    --page: #d9d9d9;
    --card: #ffffff;
    --accent: #e8592a;
    --ink: #1e1e1e;
    --sky-top: #2f7fc0;
    --sky-mid: #c9b8b0;
    --sand: #f0b46a;
    --rig: #e99a2c;
    --skin-blue: #3a6e9e;
    --helmet: #f3c51b;
  }
  * { margin: 0; padding: 0; box-sizing: border-box; }
  html, body { width: 1200px; height: 900px; overflow: hidden; }
  body {
    background: var(--page);
    font-family: "Arimo", Arial, sans-serif;
    position: relative;
  }
  .card {
    position: absolute;
    width: 540px;
    height: 310px;
    border-radius: 26px;
    overflow: hidden;
    box-shadow: 0 10px 24px rgba(0,0,0,0.22);
  }
  .card--front { left: 90px; top: 130px; }
  .card--back { left: 570px; top: 460px; background: var(--card); }

  .front-photo {
    position: absolute; inset: 0;
    background: linear-gradient(180deg, var(--sky-top) 0%, #8fb3d3 22%, var(--sky-mid) 42%, var(--sand) 68%, var(--rig) 100%);
  }
  .front-wordmark {
    position: absolute;
    left: 0; right: 0; top: 110px;
    text-align: center;
    font-weight: 700;
    font-size: 58px;
    color: #ffffff;
    letter-spacing: 0.5px;
  }

  .back-wordmark {
    position: absolute;
    left: 40px; top: 80px;
    font-weight: 700;
    font-size: 44px;
    color: var(--accent);
  }
  .back-illustration {
    position: absolute;
    right: 22px; top: 22px;
    width: 210px; height: 190px;
    border-radius: 14px;
    background: linear-gradient(160deg, #fbe9b0 0%, #f2f0ea 45%, #dfe7ef 100%);
  }
  .contact {
    position: absolute;
    left: 40px; top: 160px;
    color: var(--ink);
  }
  .contact__name {
    font-weight: 700;
    font-size: 21px;
    color: var(--accent);
    text-transform: uppercase;
    letter-spacing: 0.3px;
  }
  .contact__title { font-size: 17px; margin-top: 2px; }
  .contact__list { list-style: none; margin-top: 12px; }
  .contact__item {
    display: flex; align-items: center; gap: 10px;
    font-size: 17px; line-height: 1.45;
  }
  .contact__icon { width: 17px; height: 17px; flex: none; }
</style>
</head>
<body>
  <section class="card card--front" aria-label="Card front">
    <div class="front-photo" role="img" aria-label="Photo of orange kids' construction rides with mini excavators under a blue sky"></div>
    <div class="front-wordmark">FunBrixo</div>
  </section>

  <section class="card card--back" aria-label="Card back">
    <div class="back-wordmark">FunBrixo</div>
    <div class="back-illustration" role="img" aria-label="Illustration of two cheerful construction workers in yellow hard hats shaking hands"></div>

    <div class="contact">
      <p class="contact__name">Carl Dunning</p>
      <p class="contact__title">Co-Founder &amp; COO</p>
      <ul class="contact__list">
        <li class="contact__item">
          <svg class="contact__icon" viewBox="0 0 20 20" aria-hidden="true">
            <rect x="1" y="1" width="18" height="18" rx="3" fill="none" stroke="var(--accent)" stroke-width="2"/>
            <path d="M6 5c-1 1-1 3 1 6s4 4 6 3l1-1.5-2-1.5-1 1c-1-.5-2.5-2-3-3l1-1-1.5-2z" fill="var(--accent)"/>
          </svg>
          (833) 571-FUNBRIX
        </li>
        <li class="contact__item">
          <svg class="contact__icon" viewBox="0 0 20 20" aria-hidden="true">
            <rect x="1" y="4" width="18" height="12" fill="var(--accent)"/>
            <path d="M1 4l9 7 9-7" fill="none" stroke="#fff" stroke-width="1.6"/>
          </svg>
          Carl@funbrixo-demo.com
        </li>
        <li class="contact__item">
          <svg class="contact__icon" viewBox="0 0 20 20" aria-hidden="true">
            <circle cx="10" cy="10" r="9" fill="var(--accent)"/>
            <g fill="none" stroke="#fff" stroke-width="1.3">
              <ellipse cx="10" cy="10" rx="4" ry="9"/>
              <line x1="1" y1="10" x2="19" y2="10"/>
              <line x1="2.5" y1="6" x2="17.5" y2="6"/>
              <line x1="2.5" y1="14" x2="17.5" y2="14"/>
            </g>
          </svg>
          www.funbrixo-demo.com
        </li>
      </ul>
    </div>
  </section>
</body>
</html>
```